I would like some help creating my first business cards for my new business, I am a facilitator of a course that I have created. I am currently starting the sales promotion and marketing part of my business and need some help designing the business cards. Something fairly simple would be good, the core theme of my work is in connection of women to themselves and to each other. My initial design is a tree lit up by lights, a very mother earth type of image. This is not my design however so I probably am not legally able to use the design. I don't have a logo. Could you possibly assist with this?

I would really like to have the following details on the business card:
Meg Donlan
0431 582 917
hi.meg.donlan@larkmail.example

And also the image

Target Market(s)

Women who are living in an isolated environment

Industry/Entity Type

Counsellor

Contact Information for Business Card

Meg Donlan
Facilitator
hi.meg.donlan@larkmail.example
0431 582 917

Font styles to use
Other font styles liked:
• Handwriting - Dakota

Colors
e34197
fee18a
3276b5
33a6d7
33b8a4

Requirements
Must have
• 1) My details as above
• 2) a design (picture) that represents the mother earth theme similar to the designs included in the brief
• 3) no copyright attached to the design
• 4) Colours are very important but it is difficult to describe the colour using the colour wheel. Please refer to the example of the tree that I have included in the drop box.
• 5) I must apologise that I forgot to add the business card needs to have the name of the business in gold letters please: Riverbend Circle Gatherings Collective, thank you
Nice to have
• It would be great to use the tree design that I included in the brief, this is my favourite picture but I think it is probably copyrighted. If it's not, that is the one I would like on my business cards please.

```html
<!DOCTYPE html>
<html lang="en">
<head>
<meta charset="utf-8">
<title>Meg Donlan – Business Card</title>
<link rel="stylesheet" href="https://fonts.googleapis.com/css2?family=Parisienne&family=PT+Sans:wght@400;700&family=Open+Sans:wght@400&display=swap">
<style>
  :root {
    --backdrop: #b9e0d6;
    --card-cream: #fdfbe6;
    --card-glow: #ffffff;
    --earth-brown: #6b4a22;
    --name-brown: #4a3a28;
    --muted-grey: #7a7468;
    --gold: #f29a1c;
    --tree-violet: #b9a6e0;
    --tree-orange: #f5a23a;
    --tree-green: #9ccf8a;
    --tree-teal: #6cc2c9;
  }
  * { box-sizing: border-box; margin: 0; padding: 0; }
  html, body {
    width: 1200px; height: 856px; overflow: hidden;
    background: var(--backdrop);
  }
  .canvas {
    position: relative; width: 1200px; height: 856px;
    display: flex; align-items: center; justify-content: center;
  }
  .business-card {
    position: relative; width: 1000px; height: 572px;
    border-radius: 44px; overflow: hidden;
    background: radial-gradient(ellipse at 58% 48%, var(--card-glow) 0%, var(--card-cream) 55%, #f9f4c8 100%);
    box-shadow: 0 18px 40px rgba(40, 90, 80, 0.25);
  }
  .tree-art {
    position: absolute; left: 50px; top: 150px; width: 420px; height: 330px;
    border-radius: 50% 50% 30% 30% / 60% 60% 40% 40%;
    background:
      radial-gradient(circle at 30% 35%, var(--tree-violet) 0%, transparent 38%),
      radial-gradient(circle at 60% 30%, var(--tree-orange) 0%, transparent 42%),
      radial-gradient(circle at 75% 55%, var(--tree-teal) 0%, transparent 35%),
      radial-gradient(circle at 45% 60%, var(--tree-green) 0%, transparent 40%),
      radial-gradient(ellipse at 50% 50%, rgba(245,162,58,0.35) 0%, transparent 70%);
  }
  .earth-band {
    position: absolute; left: 0; bottom: 0; width: 1000px; height: 572px;
  }
  .holder {
    position: absolute; right: 240px; top: 44px; text-align: right;
  }
  .holder-name {
    font-family: "PT Sans", sans-serif; font-weight: 700;
    font-size: 30px; color: var(--name-brown); line-height: 1;
  }
  .holder-role {
    font-family: "PT Sans", sans-serif; font-weight: 400;
    font-size: 19px; color: var(--muted-grey); line-height: 1.1;
    margin-right: -12px;
  }
  .business-name {
    position: absolute; left: 520px; top: 120px;
    font-family: "Parisienne", cursive; font-size: 52px; line-height: 58px;
    font-weight: 400; color: var(--gold);
  }
  .business-name span { display: block; }
  .business-name .line-2 { padding-left: 40px; }
  .business-name .line-3 { padding-left: 75px; }
  .contact-row {
    position: absolute; left: 470px; top: 318px;
    display: flex; gap: 20px; align-items: center;
    font-family: "Open Sans", sans-serif; font-size: 17px; color: var(--name-brown);
    white-space: nowrap;
  }
  .contact-item { display: flex; align-items: center; gap: 8px; }
  .contact-icon { width: 20px; height: 20px; flex: none; }
</style>
</head>
<body>
<main class="canvas">
  <section class="business-card">
    <div class="tree-art" role="img" aria-label="Illustration of a tree with swirling coloured rings and star-shaped flowers"></div>

    <svg class="earth-band" viewBox="0 0 1000 572" aria-hidden="true">
      <path d="M0 565 C 200 530, 320 510, 470 480 S 800 420, 1000 385 L 1000 572 L 0 572 Z" fill="var(--earth-brown)"/>
    </svg>

    <header class="holder">
      <p class="holder-name">Meg Donlan</p>
      <p class="holder-role">Facilitator</p>
    </header>

    <h1 class="business-name">
      <span class="line-1">Riverbend Circle</span>
      <span class="line-2">Gatherings</span>
      <span class="line-3">Collective</span>
    </h1>

    <div class="contact-row">
      <p class="contact-item">
        <svg class="contact-icon" viewBox="0 0 24 24" aria-hidden="true">
          <circle cx="12" cy="12" r="11" fill="none" stroke="var(--name-brown)" stroke-width="1.6"/>
          <path d="M6 10c0-2 3-3 6-3s6 1 6 3v1h-3v-1.5H9V11H6z M8 12h8l1 5H7z" fill="var(--name-brown)"/>
        </svg>
        0431 582 917
      </p>
      <p class="contact-item">
        <svg class="contact-icon" viewBox="0 0 24 24" aria-hidden="true">
          <circle cx="12" cy="12" r="11" fill="none" stroke="var(--name-brown)" stroke-width="1.6"/>
          <rect x="6" y="8" width="12" height="8" fill="var(--name-brown)"/>
          <path d="M6 8l6 5 6-5" fill="none" stroke="var(--card-cream)" stroke-width="1.2"/>
        </svg>
        hi.meg.donlan@larkmail.example
      </p>
    </div>
  </section>
</main>
</body>
</html>
```